Maple Roster Business Card for recruitment company

We are looking for a Business Card Design that incorporates our personal details and our busines name and logo. We are a specialized search consultancy that recruit Property and Construction professionals.
We would like a business card that stands out and is appealing to the Construction and Property industry as well.

Target Market(s)

people in the construction and property industry

Contact Information for Business Card

Business Name and logo

Font styles to use
Serif

Colors
0094D4
00A9DD
6FCCEA
C7EBF8
E9F6FB

Requirements
Must have
• Business name and logo as well as contact details
Should not have
• No photos of us please

```html
<!DOCTYPE html>
<html lang="en">
<head>
<meta charset="utf-8">
<title>Maple Roster – Business Card</title>
<link href="https://fonts.googleapis.com/css2?family=Montserrat:wght@300;400;600&display=swap" rel="stylesheet">
<style>
  :root {
    --backdrop: #d0d0d0;
    --card-white: #ffffff;
    --brand-teal: #033b4e;
    --name-teal: #0b3f55;
    --text-dark: #333333;
    --text-muted: #4a4a4a;
    --rule: #7fa3b4;
  }
  * { margin: 0; padding: 0; box-sizing: border-box; }
  html, body {
    width: 900px; height: 1200px; overflow: hidden;
    background: var(--backdrop);
    font-family: "Montserrat", Arial, sans-serif;
  }
  .canvas { position: relative; width: 900px; height: 1200px; }
  .card {
    position: absolute; left: 79px; width: 743px;
    box-shadow: 0 8px 22px rgba(0,0,0,0.28);
  }
  .card-front { top: 131px; height: 441px; background: var(--card-white); overflow: hidden; }
  .card-back { top: 638px; height: 440px; background: var(--brand-teal); }

  .front-band {
    position: absolute; left: 0; right: 0; bottom: 0; height: 12px;
    background: var(--brand-teal);
  }
  .front-wordmark {
    position: absolute; right: 56px; top: 52px;
    font-size: 43px; font-weight: 400; letter-spacing: 1px;
    color: var(--brand-teal); white-space: nowrap;
  }
  .person-name {
    position: absolute; left: 40px; top: 255px;
    font-size: 25px; font-weight: 600; color: var(--name-teal);
  }
  .person-title {
    position: absolute; left: 40px; top: 288px;
    font-size: 16px; font-weight: 400; color: var(--text-muted);
  }
  .divider {
    position: absolute; left: 40px; top: 314px; width: 647px; height: 1px;
    background: var(--rule);
  }
  .contact-list { position: absolute; left: 38px; top: 332px; list-style: none; }
  .contact-item {
    display: flex; align-items: center; height: 24px;
    font-size: 16px; color: var(--text-dark);
  }
  .contact-icon { width: 14px; height: 14px; margin-right: 17px; fill: var(--brand-teal); }
  .address {
    position: absolute; left: 507px; top: 358px;
    font-size: 16px; line-height: 21px; color: var(--text-dark); font-style: normal;
  }
  .back-wordmark {
    position: absolute; left: 0; right: 0; top: 185px; text-align: center;
    font-size: 62px; font-weight: 400; letter-spacing: 2px;
    color: var(--card-white); white-space: nowrap;
  }
</style>
</head>
<body>
<main class="canvas">
  <section class="card card-front" aria-label="Business card front">
    <div class="front-wordmark">MAPLE ROSTER</div>
    <h1 class="person-name">Dana Whitfield</h1>
    <p class="person-title">Owner/ Designer</p>
    <div class="divider"></div>
    <ul class="contact-list">
      <li class="contact-item">
        <svg class="contact-icon" viewBox="0 0 16 16" aria-hidden="true"><path d="M1 5c0-2 3-3 7-3s7 1 7 3v1h-4V4.5H5V6H1zM3 7h10l1 7H2z"/></svg>
        (555) 204-3817
      </li>
      <li class="contact-item">
        <svg class="contact-icon" viewBox="0 0 16 16" aria-hidden="true"><path d="M1 4h14v1L8 9 1 5zM1 6.5l7 4 7-4V13H1z"/></svg>
        info@mapleroster.com
      </li>
      <li class="contact-item">
        <svg class="contact-icon" viewBox="0 0 16 16" aria-hidden="true"><circle cx="8" cy="8" r="7"/><path d="M4 5c2 0 2 2 4 2s0 3 2 3-1 3-2 4M10 2c0 2 2 2 3 3" stroke="#fff" stroke-width="1.2" fill="none"/></svg>
        www.mapleroster.com
      </li>
    </ul>
    <address class="address">82 Harbor Lane<br>Cedar Point, CA 90210</address>
    <div class="front-band"></div>
  </section>

  <section class="card card-back" aria-label="Business card back">
    <div class="back-wordmark">MAPLE ROSTER</div>
  </section>
</main>
</body>
</html>
```